Real Estate Business Card

On the front side I want to have my info, my brokerage info.
On the back side I want have my complany’s logo, website and Facebook link. I will provide all this once I select a design.

I would like to see Black background and gold text, Dark Blue and gold text and White and blue text designs

Font styles to use
Sans Serif
Script

```html
<!DOCTYPE html>
<html lang="en">
<head>
<meta charset="utf-8">
<title>Keystone Ridge Realty – Business Card</title>
<link rel="stylesheet" href="https://fonts.googleapis.com/css2?family=Montserrat:wght@500;700;800&family=Roboto:wght@400;500&display=swap">
<style>
  :root {
    --backdrop: #2b2c2f;
    --card: #1c1d20;
    --brand-red: #e03a3e;
    --wordmark-grey: #8d939e;
    --gold: #e2b33c;
    --white: #f4f4f4;
  }
  * { margin: 0; padding: 0; box-sizing: border-box; }
  html, body { width: 1200px; height: 900px; overflow: hidden; }
  body {
    background: var(--backdrop);
    display: flex;
    flex-direction: column;
    align-items: center;
    justify-content: center;
    gap: 40px;
    font-family: "Roboto", Arial, sans-serif;
  }
  .card {
    position: relative;
    width: 660px;
    height: 360px;
    background: var(--card);
    border-radius: 4px;
    overflow: hidden;
  }

  /* Back side: brand and website */
  .card--back {
    display: flex;
    flex-direction: column;
    align-items: center;
    justify-content: center;
  }
  .brand {
    display: flex;
    align-items: center;
    gap: 14px;
  }
  .brand__square {
    width: 46px;
    height: 46px;
    background: var(--brand-red);
  }
  .brand__name {
    font-family: "Montserrat", Arial, sans-serif;
    font-weight: 800;
    font-size: 44px;
    line-height: 1;
    color: var(--wordmark-grey);
    text-transform: uppercase;
  }
  .brand__tagline {
    font-family: "Montserrat", Arial, sans-serif;
    font-weight: 800;
    font-size: 15px;
    letter-spacing: 0.55em;
    color: var(--wordmark-grey);
    text-transform: uppercase;
    margin-top: 8px;
  }
  .website {
    margin-top: 40px;
    font-family: "Montserrat", Arial, sans-serif;
    font-weight: 500;
    font-size: 17px;
    letter-spacing: 0.45em;
    color: var(--white);
  }

  /* Front side: agent details */
  .card--front { padding: 30px 34px; }
  .card--front .brand__name { font-size: 30px; }
  .card--front .brand__tagline { font-size: 11px; letter-spacing: 0.5em; margin-top: 5px; }
  .agent { margin-top: 52px; }
  .agent__name {
    font-family: "Montserrat", Arial, sans-serif;
    font-weight: 700;
    font-size: 24px;
    color: var(--gold);
    text-transform: uppercase;
  }
  .agent__role {
    font-family: "Montserrat", Arial, sans-serif;
    font-weight: 500;
    font-size: 15px;
    color: var(--brand-red);
    text-transform: uppercase;
    margin-top: 2px;
  }
  .contact {
    list-style: none;
    margin-top: 18px;
    font-size: 16px;
    line-height: 1.4;
    color: var(--white);
  }
  .contact__address { margin-bottom: 8px; }
  .contact__label { color: var(--gold); font-weight: 500; margin-right: 4px; }
  .brand-block {
    position: absolute;
    right: 36px;
    bottom: 0;
    width: 250px;
    height: 280px;
    background: var(--brand-red);
  }
</style>
</head>
<body>
  <section class="card card--back">
    <div class="brand">
      <span class="brand__square"></span>
      <span class="brand__name">Keystone Ridge</span>
    </div>
    <div class="brand__tagline">Realty</div>
    <div class="website">www.keystoneridge.com</div>
  </section>

  <section class="card card--front">
    <div class="brand__name">Keystone Ridge</div>
    <div class="brand__tagline">Realty</div>

    <div class="agent">
      <div class="agent__name">Daniel Hart</div>
      <div class="agent__role">CEO/Founder</div>
    </div>

    <ul class="contact">
      <li class="contact__address">4120 Birchwood Avenue<br>Juneau, Alaska 99801</li>
      <li><span class="contact__label">P:</span>555 201 4832</li>
      <li><span class="contact__label">M:</span>555 307 9146</li>
      <li><span class="contact__label">E:</span>daniel@keystoneridge.com</li>
    </ul>

    <div class="brand-block" role="img" aria-label="Large brand decoration area"></div>
  </section>
</body>
</html>
```